Re-style home page - eye-catching and unique design for social commerce website

We need a new concept design for BrinoKet's home page.
We don't want to make huge changes but creating a more professional and eye-catching style.

We need to look very serious like a professional services company and in the same time to look like a social network for e-commerce.

Our logo is very captive and you can use to creating something of harmonious.

This is a re-style and I'm excepted to see unique and fresh design like Glimmora.

Target Market(s)

e-commerce and social

Industry/Entity Type

Social

Number of Pages Required

1 page

Font styles to use
Serif
Sans Serif

Requirements
Must have
• An eye-catching result.
• Search bar with logo and Login How it works and business
• The slogan with login and signup.
• Footer links.
Nice to have
• I would like to open the home page and see only two clear ways:
• -Consumer
• --Search
• --The slogan
• --Login and Signup
• --How it works
• -Business
• --Go to Business area
• Background: City, Shopping.
Should not have
• Scrollbar style!

```html
<!DOCTYPE html>
<html lang="en">
<head>
<meta charset="utf-8">
<title>BrinoKet – Shop Directly From Your Profile</title>
<link rel="stylesheet" href="https://fonts.googleapis.com/css2?family=Open+Sans:wght@400;600;700&display=swap">
<style>
  :root {
    --ink: #ffffff;
    --header-bg: #121212;
    --nav-text: #c9c9c9;
    --scene-dark: #2a2622;
    --scene-mid: #5a5047;
    --panel-light: #b9a48c;
    --panel-dark: #6f5f50;
    --tag-bg: rgba(20, 18, 16, 0.82);
    --social-blue: #2d4f9e;
    --social-blue-dark: #24418a;
    --footer-bg: #ffffff;
    --footer-text: #707070;
  }
  * { box-sizing: border-box; margin: 0; padding: 0; }
  html, body { width: 1200px; height: 801px; overflow: hidden; }
  body { font-family: "Open Sans", Arial, sans-serif; color: var(--ink); position: relative; background: var(--scene-dark); }

  .site-header {
    position: absolute; left: 0; top: 0; width: 1200px; height: 80px;
    background: linear-gradient(#1a1a1a, var(--header-bg));
    z-index: 2;
  }
  .brand {
    position: absolute; left: 113px; top: 16px;
    font-size: 36px; font-weight: 700; letter-spacing: -1px; color: var(--ink);
    line-height: 48px;
  }
  .search {
    position: absolute; left: 339px; top: 22px; width: 370px; height: 36px;
    background: #fff; padding: 0 11px;
    font: 400 13px "Open Sans", Arial, sans-serif; color: #888;
    display: flex; align-items: center;
  }
  .main-nav {
    position: absolute; left: 726px; top: 23px; height: 34px;
    display: flex; align-items: center; font-size: 14.5px; color: var(--nav-text);
    white-space: nowrap;
  }
  .main-nav .sep { margin: 0 12px; }
  .main-nav .cta {
    margin-left: 13px; width: 107px; height: 34px;
    border: 1px solid #8a8a8a; border-radius: 2px;
    display: flex; align-items: center; justify-content: center;
  }

  .hero-scene {
    position: absolute; left: 0; top: 80px; width: 1200px; height: 680px;
    background: radial-gradient(ellipse at 50% 40%, var(--scene-mid), var(--scene-dark) 75%);
  }
  .hero-title {
    position: absolute; top: 134px; width: 1200px; text-align: center;
    font-size: 32px; font-weight: 600; text-shadow: 0 2px 4px rgba(0,0,0,.6);
  }

  .feed-panel {
    position: absolute; left: 247px; top: 226px; width: 706px; height: 456px;
    border-radius: 4px; overflow: hidden;
  }
  .feed-photo {
    position: absolute; inset: 0;
    background: linear-gradient(160deg, var(--panel-light) 0%, #9a8670 45%, var(--panel-dark) 100%);
  }
  .panel-login {
    position: absolute; left: 600px; top: 15px; width: 90px; height: 37px;
    background: linear-gradient(#ffffff, #dcdcdc); border-radius: 3px;
    color: #2a2a2a; font-size: 17px; font-weight: 700;
    display: flex; align-items: center; justify-content: center;
    box-shadow: 0 1px 3px rgba(0,0,0,.4);
  }
  .feed-title {
    position: absolute; top: 30px; width: 706px; text-align: center;
    font-size: 32px; font-weight: 600; text-shadow: 0 2px 4px rgba(0,0,0,.5);
  }
  .category-list { position: absolute; left: 12px; top: 87px; }
  .category-row { display: flex; gap: 7px; margin-bottom: 11px; }
  .category {
    height: 37px; padding: 0 9px 0 7px; background: var(--tag-bg); border-radius: 2px;
    display: flex; align-items: center; gap: 7px; font-size: 15px; font-weight: 600; white-space: nowrap;
  }
  .category svg { width: 17px; height: 17px; flex: none; }
  .tagline {
    position: absolute; top: 334px; width: 706px; text-align: center;
    font-size: 22px; font-weight: 600; text-shadow: 0 1px 3px rgba(0,0,0,.5);
  }
  .social-login {
    position: absolute; left: 242px; top: 372px; width: 222px; height: 40px;
    background: var(--social-blue); display: flex; align-items: center; font-size: 16px; font-weight: 600;
    white-space: nowrap;
  }
  .social-login .mark { width: 40px; height: 40px; background: var(--social-blue-dark); margin-right: 15px; flex: none; }
  .signup-link { position: absolute; top: 420px; width: 706px; text-align: center; font-size: 16px; font-weight: 600; }

  .site-footer {
    position: absolute; left: 0; top: 760px; width: 1200px; height: 41px;
    background: var(--footer-bg); border-top: 1px solid #ddd;
    display: flex; justify-content: center; align-items: center; gap: 18px;
    font-size: 14.5px; color: var(--footer-text);
  }
</style>
</head>
<body>
  <header class="site-header">
    <div class="brand">BrinoKet</div>
    <div class="search">Search here...</div>
    <nav class="main-nav">
      <span>How It Works</span><span class="sep">|</span>
      <span>Business</span><span class="sep">|</span>
      <span>Login</span>
      <span class="cta">Sign Up Now</span>
    </nav>
  </header>

  <div class="hero-scene" role="img" aria-label="Busy shopping mall with escalators and shoppers"></div>
  <h1 class="hero-title">Shop Directly From Your Profile</h1>

  <section class="feed-panel">
    <div class="feed-photo" role="img" aria-label="City skyline seen over a person's shoulder"></div>
    <div class="panel-login">LOGIN</div>
    <h2 class="feed-title">Setup Your Feed</h2>

    <svg width="0" height="0" style="position:absolute">
      <symbol id="tick" viewBox="0 0 17 17">
        <circle cx="8.5" cy="8.5" r="8.5" fill="#bdbdbd"/>
        <path d="M4.6 8.8l2.6 2.6 5.2-5.4" fill="none" stroke="#2a2622" stroke-width="2"/>
      </symbol>
    </svg>

    <div class="category-list">
      <div class="category-row">
        <span class="category"><svg><use href="#tick"/></svg>Active Life</span>
        <span class="category"><svg><use href="#tick"/></svg>Education</span>
        <span class="category"><svg><use href="#tick"/></svg>Health &amp; Medical</span>
        <span class="category"><svg><use href="#tick"/></svg>Public Services &amp; Government</span>
      </div>
      <div class="category-row">
        <span class="category"><svg><use href="#tick"/></svg>Art &amp; Entertainment</span>
        <span class="category"><svg><use href="#tick"/></svg>Event Planning &amp; Services</span>
        <span class="category"><svg><use href="#tick"/></svg>Home Services</span>
        <span class="category"><svg><use href="#tick"/></svg>Pets</span>
      </div>
      <div class="category-row">
        <span class="category"><svg><use href="#tick"/></svg>Automative</span>
        <span class="category"><svg><use href="#tick"/></svg>Financial Services</span>
        <span class="category"><svg><use href="#tick"/></svg>Hotels</span>
        <span class="category"><svg><use href="#tick"/></svg>Professional Services</span>
      </div>
      <div class="category-row">
        <span class="category"><svg><use href="#tick"/></svg>Beauty &amp; Spas</span>
        <span class="category"><svg><use href="#tick"/></svg>Local Services</span>
        <span class="category"><svg><use href="#tick"/></svg>Mass Media</span>
        <span class="category"><svg><use href="#tick"/></svg>Nighlife</span>
        <span class="category"><svg><use href="#tick"/></svg>Food</span>
      </div>
      <div class="category-row">
        <span class="category"><svg><use href="#tick"/></svg>Real Estate</span>
        <span class="category"><svg><use href="#tick"/></svg>Restaurants</span>
        <span class="category"><svg><use href="#tick"/></svg>Shopping</span>
      </div>
    </div>

    <p class="tagline">Save your time. Live Better.</p>
    <div class="social-login"><span class="mark"></span>Login With Friendlane</div>
    <p class="signup-link">Sign Up</p>
  </section>

  <footer class="site-footer">
    <span>About Us</span><span>Blog</span><span>Business</span><span>Jobs</span>
    <span>Privacy</span><span>FAQ</span><span>Contacts</span>
  </footer>
</body>
</html>
```